Moldran Foods needs a new label for canned pineapple

We want a very tasty (in terms of making your mouth water) and clean design (less is more) for our canned pineapple under the new logo of Moldran Leafline division

Target Market(s)

The company’s mission is to bring quality food to target audiences of any social status (you receive a bit more than what you spend). Our core values are: reliability, loyalty and commitment to development.
The product is sold to mainstream and lower Mainstream customers.

Requirements
Must have
• The design should take into consideration the visibility on the shelf among competitor products (brief file) and that the product is a MAINSTREAM product.
We want a very tasty (in terms of making your mouth water) and clean design (less is more). The design should be easily modifiable for other canned fruits or vegetables.
The package must display on the front the following elements listed in the order of their should have noticeability:
• Moldran Leaf logo
• Pineapple picture
• Product name
Designers should take into account that the shelfs for displaying the products in the shops may have an elevation of up to 3 cm that can overlap the product label.

Guidelines
• We would like the packaging to be as simple as possible (or at least not to sabotage the Moldran name ), as our strategy depends on the agressive communication of the Moldran logo.
• We would also like to communicate through suggestive and optimal colours as to be easily spotted on the shelf.
• As we have quite a minimal communication budget we need basically for the packaging to do a lot of the communication job itself
• FMCG is a highly visual industry so we have to include pictures of the products on the packages (even more than others do, as we are focused on health and quality - we want people to have that feeling of fresh products even though we are selling canned ones)
Should not have
• but the minimum amount of text on the front.

```html
<!DOCTYPE html>
<html lang="ro">
<head>
<meta charset="utf-8">
<title>Moldran Leafline – ananas felii</title>
<link rel="stylesheet" href="https://fonts.googleapis.com/css2?family=Roboto:wght@300;700&display=swap">
<style>
  :root {
    --backdrop: #e4e4e4;
    --label-white: #ffffff;
    --fruit-light: #fbeeb4;
    --fruit-mid: #f1d97e;
    --fruit-edge: #e2c15a;
    --title-white: #ffffff;
    --brand-green: #1f7a3c;
    --weight-grey: #8a8a8a;
  }
  html, body {
    margin: 0;
    width: 1200px;
    height: 900px;
    overflow: hidden;
    background: var(--backdrop);
    font-family: "Roboto", Arial, sans-serif;
  }
  .label {
    position: absolute;
    left: 357px;
    top: 159px;
    width: 486px;
    height: 582px;
    background: var(--label-white);
    box-shadow: 0 2px 10px rgba(0,0,0,0.08);
  }
  .fruit-photo {
    position: absolute;
    left: 75px;
    top: 32px;
    width: 336px;
    height: 336px;
    border-radius: 50%;
    background: radial-gradient(circle at 50% 50%, var(--fruit-light) 0%, var(--fruit-mid) 70%, var(--fruit-edge) 100%);
  }
  .product-name {
    position: absolute;
    left: 0;
    width: 100%;
    top: 138px;
    margin: 0;
    text-align: center;
    color: var(--title-white);
    font-weight: 700;
    font-size: 72px;
    line-height: 64px;
    letter-spacing: -1px;
  }
  .brand {
    position: absolute;
    left: 0;
    width: 100%;
    top: 418px;
    display: flex;
    align-items: center;
    justify-content: center;
    gap: 10px;
  }
  .brand-dot {
    width: 18px;
    height: 18px;
    border-radius: 50%;
    background: var(--brand-green);
  }
  .brand-name {
    color: var(--brand-green);
    font-weight: 700;
    font-size: 28px;
  }
  .net-weight {
    position: absolute;
    right: 48px;
    top: 540px;
    margin: 0;
    color: var(--weight-grey);
    font-weight: 300;
    font-size: 19px;
  }
</style>
</head>
<body>
  <div class="label">
    <div class="fruit-photo" role="img" aria-label="Photo of a fresh pineapple slice seen from above"></div>
    <h1 class="product-name">ananas<br>felii</h1>
    <div class="brand">
      <span class="brand-dot"></span>
      <span class="brand-name">Moldran Leafline</span>
    </div>
    <p class="net-weight">285g 175g(uscat)</p>
  </div>
</body>
</html>
```